New Bicycle shop business card

Hi!
I'm looking for a business card for my new proffesional bike mechanics shop. This shop is only for fixing broken bikes and not selling bikes.
Peferbly a modern and sleek and modern design.
Colors: black, grey, red, white
Information:
Name: Rijwielwerkplaats Vanhoutte
Shop owner: Bart Vanhoutte & Marieke Segers
Website: www.rijwielwerkplaats-vanhoutte.be
Email: info@rijwielwerkplaats-vanhoutte.be
Phone number: +32471902368
Street adres: Kerkweg 46
9940 Bellebeke
Slogan/shop information: Herstellingen van alle merken.
Logo: see files.
Target Market(s)
People who seek a mechanic to fix or upgrade their bikes.
Contact Information for Business Card
Information:
Website: info@rijwielwerkplaats-vanhoutte.be
9940 Bellebeke
Logo: see files.

```html
<!DOCTYPE html>
<html lang="nl">
<head>
<meta charset="utf-8">
<title>Rijwielwerkplaats Vanhoutte – Visitekaartje</title>
<link href="https://fonts.googleapis.com/css2?family=Montserrat:wght@500;700;800&family=Roboto:wght@400;500&display=swap" rel="stylesheet">
<style>
  :root {
    --backdrop: #e4e4e4;
    --card: #ffffff;
    --ink: #1c1c1c;
    --red: #d8283a;
    --grey: #8e9296;
    --text: #2b2b2b;
  }
  * { box-sizing: border-box; margin: 0; padding: 0; }
  html, body {
    width: 1200px; height: 852px; overflow: hidden;
    background: var(--backdrop);
  }
  .stage {
    position: relative; width: 1200px; height: 852px;
    display: flex; align-items: center; justify-content: center; gap: 60px;
  }
  .card {
    position: relative; width: 510px; height: 330px;
    background: var(--card); border-radius: 18px; overflow: hidden;
    box-shadow: 0 10px 28px rgba(0,0,0,.14);
    font-family: "Roboto", Arial, sans-serif; color: var(--text);
  }

  /* Front */
  .front-brand {
    position: absolute; top: 62px; left: 0; right: 0;
    display: flex; flex-direction: column; align-items: center; gap: 16px;
  }
  .brand-mark { width: 48px; height: 48px; background: var(--red); border-radius: 50%; flex: none; }
  .brand-name {
    font-family: "Montserrat", Arial, sans-serif; font-weight: 800;
    color: var(--ink); text-transform: uppercase; text-align: center;
    font-size: 25px; line-height: 1.15; letter-spacing: 1.5px;
    white-space: nowrap;
  }
  .tagline {
    position: absolute; top: 236px; left: 0; right: 0;
    display: flex; align-items: center; justify-content: center; gap: 12px;
    font-size: 14px; color: var(--text);
  }
  .tagline::before, .tagline::after {
    content: ""; width: 54px; height: 2px; background: var(--red);
  }
  .edge-band { position: absolute; left: 0; bottom: 0; width: 100%; height: 12px; }

  /* Back */
  .holder { position: absolute; top: 52px; left: 40px; }
  .holder-name {
    font-family: "Montserrat", Arial, sans-serif; font-weight: 700;
    color: var(--red); text-transform: uppercase; font-size: 21px; letter-spacing: .5px;
    white-space: nowrap;
  }
  .holder-role { font-size: 13px; margin-top: 4px; }
  .back-brand {
    position: absolute; top: 92px; right: 30px;
    display: flex; flex-direction: column; align-items: center; gap: 10px;
  }
  .back-brand .brand-mark { width: 40px; height: 40px; }
  .back-brand .brand-name { font-size: 17px; letter-spacing: 1px; }
  .contact-list {
    position: absolute; left: 40px; bottom: 36px; list-style: none;
    display: flex; flex-direction: column; gap: 7px; font-size: 14px;
  }
  .contact-list li { display: flex; align-items: center; gap: 10px; white-space: nowrap; }
  .contact-list svg { width: 14px; height: 14px; fill: var(--red); flex: none; }
</style>
</head>
<body>
<main class="stage">

  <section class="card card-front" aria-label="Voorkant">
    <div class="front-brand">
      <span class="brand-mark"></span>
      <p class="brand-name">Rijwielwerkplaats<br>Vanhoutte</p>
    </div>
    <p class="tagline">Herstellingen van alle merken</p>
    <svg class="edge-band" viewBox="0 0 510 12" preserveAspectRatio="none" aria-hidden="true">
      <polygon points="0,0 300,0 290,12 0,12" fill="var(--red)"/>
      <polygon points="300,0 510,0 510,12 290,12" fill="var(--grey)"/>
    </svg>
  </section>

  <section class="card card-back" aria-label="Achterkant">
    <div class="holder">
      <p class="holder-name">Marieke Segers</p>
      <p class="holder-role">Owner</p>
    </div>

    <div class="back-brand">
      <span class="brand-mark"></span>
      <p class="brand-name">Rijwielwerkplaats<br>Vanhoutte</p>
    </div>

    <ul class="contact-list">
      <li>
        <svg viewBox="0 0 24 24" aria-hidden="true"><path d="M6.6 10.8a15.1 15.1 0 0 0 6.6 6.6l2.2-2.2a1 1 0 0 1 1-.25 11.4 11.4 0 0 0 3.6.57 1 1 0 0 1 1 1V20a1 1 0 0 1-1 1A17 17 0 0 1 3 4a1 1 0 0 1 1-1h3.5a1 1 0 0 1 1 1c0 1.25.2 2.45.57 3.57a1 1 0 0 1-.25 1z"/></svg>
        +32471902368
      </li>
      <li>
        <svg viewBox="0 0 24 24" aria-hidden="true"><path d="M12 2a10 10 0 1 0 0 20 10 10 0 0 0 0-20zm6.9 6h-2.9a15.7 15.7 0 0 0-1.4-3.6A8 8 0 0 1 18.9 8zM12 4c.8 1.2 1.5 2.5 1.9 4h-3.8c.4-1.5 1.1-2.8 1.9-4zM4.3 14a8.2 8.2 0 0 1 0-4h3.4a16 16 0 0 0 0 4zm.8 2h2.9c.3 1.3.8 2.5 1.4 3.6A8 8 0 0 1 5.1 16zM8 8H5.1a8 8 0 0 1 4.3-3.6C8.8 5.5 8.3 6.7 8 8zm4 12c-.8-1.2-1.5-2.5-1.9-4h3.8c-.4 1.5-1.1 2.8-1.9 4zm2.3-6H9.7a14.7 14.7 0 0 1 0-4h4.6a14.7 14.7 0 0 1 0 4zm.3 5.6c.6-1.1 1.1-2.3 1.4-3.6h2.9a8 8 0 0 1-4.3 3.6zm1.7-5.6a16 16 0 0 0 0-4h3.4a8.2 8.2 0 0 1 0 4z"/></svg>
        www.rijwielwerkplaats-vanhoutte.be
      </li>
      <li>
        <svg viewBox="0 0 24 24" aria-hidden="true"><path d="M20 4H4a2 2 0 0 0-2 2v12a2 2 0 0 0 2 2h16a2 2 0 0 0 2-2V6a2 2 0 0 0-2-2zm0 4-8 5-8-5V6l8 5 8-5z"/></svg>
        info@rijwielwerkplaats-vanhoutte.be
      </li>
      <li>
        <svg viewBox="0 0 24 24" aria-hidden="true"><path d="M12 2a7 7 0 0 0-7 7c0 5.2 7 13 7 13s7-7.8 7-13a7 7 0 0 0-7-7zm0 9.5a2.5 2.5 0 1 1 0-5 2.5 2.5 0 0 1 0 5z"/></svg>
        Kerkweg 46 9940 Bellebeke
      </li>
    </ul>
  </section>

</main>
</body>
</html>
```